Meridale Real Estate

We are looking for help with web design for a new company that is revolutionizing the real estate world on the listing side: by charing per hour for top level professional real estate services. We would like the concept to be simple, clean and easily understood.
Updates

We want this website to actually function, not just a static design.

Industry/Entity Type

Real Estate

```html
<!DOCTYPE html>
<html lang="en">
<head>
<meta charset="utf-8">
<title>Meridale Real Estate</title>
<link rel="stylesheet" href="https://fonts.googleapis.com/css2?family=Roboto+Condensed:wght@400;700&family=Arimo:wght@400&display=swap">
<style>
:root{
  --ink:#ffffff;
  --night:#0f1a2e;
  --accent:#29a8e0;
  --slate:#4b4b4b;
  --footer:#1c1c1c;
  --footer-text:#9a9a9a;
  --social:#6e6e6e;
}
*{margin:0;padding:0;box-sizing:border-box}
html,body{width:1200px;height:816px;overflow:hidden;background:var(--footer)}
body{font-family:"Roboto Condensed",Arial,sans-serif;color:var(--ink);position:relative}
.hero{position:absolute;left:0;top:0;width:1200px;height:740px;
  background:
   radial-gradient(ellipse 520px 300px at 840px 430px,rgba(214,150,70,.55),transparent 70%),
   linear-gradient(180deg,#0c1424 0%,#1c2f52 30%,#3d5b86 45%,#1a2433 62%,#0b0f16 100%)}
.brand{position:absolute;left:200px;top:46px;display:flex;align-items:center;gap:10px;
  font-size:15px;line-height:20px;font-weight:400;letter-spacing:3px;text-transform:uppercase;color:var(--ink)}
.brand-dot{width:16px;height:16px;border:2px solid var(--ink);border-radius:50%;flex:none}
.nav{position:absolute;top:74px;left:0;font-size:15px;font-weight:700;text-transform:uppercase}
.nav a{position:absolute;color:var(--ink);text-decoration:none;white-space:nowrap}
.nav a.active::before{content:"";position:absolute;left:-12px;top:-19px;width:55px;height:2px;background:var(--accent)}
.headline{position:absolute;left:176px;top:418px;font-size:25px;line-height:37px;font-weight:400;text-transform:uppercase;letter-spacing:.2px}
.slider-arrows{position:absolute;left:937px;top:496px;width:83px;height:40px;background:rgba(120,120,120,.45);display:flex}
.slider-arrows svg{width:41px;height:40px}
.tiles{position:absolute;left:181px;top:549px;display:flex;height:172px}
.tile-photo{width:206px;height:172px}
.photo-home{background:linear-gradient(160deg,#1f3550 0%,#56708c 40%,#3d3525 75%,#6b5a35 100%)}
.photo-office{background:linear-gradient(180deg,#9fc7e0 0%,#c7dceb 40%,#7c97a8 70%,#3e5c6d 100%);margin-left:20px}
.tile-text{width:204px;height:172px;padding:24px 16px 0;text-align:center}
.tile-text h2{font-size:15px;font-weight:400;letter-spacing:1.6px;text-transform:uppercase;margin-bottom:16px}
.tile-text p{font-family:Arimo,Arial,sans-serif;font-size:11.5px;line-height:20.5px}
.tile-blue{background:var(--accent)}
.tile-grey{background:var(--slate)}
.footer{position:absolute;left:0;top:740px;width:1200px;height:76px;background:var(--footer)}
.footer-nav{position:absolute;left:187px;top:19px;display:flex;gap:26px;font-family:Arimo,Arial,sans-serif;font-size:11px;text-transform:uppercase}
.footer-nav a{color:var(--footer-text);text-decoration:none}
.copyright{position:absolute;left:187px;top:48px;font-family:Arimo,Arial,sans-serif;font-size:8px;color:#cfcfcf}
.social{position:absolute;left:918px;top:25px;display:flex;gap:4px}
.social span{width:22px;height:22px;border-radius:50%;background:var(--social)}
</style>
</head>
<body>
<div class="hero" role="img" aria-label="Photograph of a modern luxury villa with a lit pool terrace at dusk"></div>

<header>
  <div class="brand"><span class="brand-dot"></span><span>Meridale<br>Real Estate</span></div>
  <nav class="nav">
    <a class="active" href="#" style="left:467px">Home</a>
    <a href="#" style="left:539px">Commercial</a>
    <a href="#" style="left:651px">Residential</a>
    <a href="#" style="left:759px">Farm</a>
    <a href="#" style="left:828px">Vacant Land</a>
    <a href="#" style="left:941px">Contact</a>
  </nav>
</header>

<main>
  <h1 class="headline">We sell luxury homes, office buildings,<br>farms, and ranches.</h1>
  <div class="slider-arrows">
    <svg viewBox="0 0 41 40"><path d="M24 11 L15 20 L24 29" fill="none" stroke="#fff" stroke-width="1.5"/></svg>
    <svg viewBox="0 0 41 40"><path d="M17 11 L26 20 L17 29" fill="none" stroke="#fff" stroke-width="1.5"/></svg>
  </div>
  <section class="tiles">
    <div class="tile-photo photo-home" role="img" aria-label="Photograph of a modern luxury home at night"></div>
    <article class="tile-text tile-blue">
      <h2>Luxury Homes</h2>
      <p>uncover many web sites still in their infancy. Various versions have evolved over the years, sometimes by accident...</p>
    </article>
    <div class="tile-photo photo-office" role="img" aria-label="Photograph of glass office towers on a waterfront"></div>
    <article class="tile-text tile-grey">
      <h2>Office Buildings</h2>
      <p>uncover many web sites still in their infancy. Various versions have evolved over the years, sometimes by accident...</p>
    </article>
  </section>
</main>

<footer class="footer">
  <nav class="footer-nav">
    <a href="#">Home</a><a href="#">Commercial</a><a href="#">Residential</a><a href="#">Farm</a><a href="#">Vacant Land</a><a href="#">Contact</a>
  </nav>
  <p class="copyright">© Copyrights 2015 Meridale Real Estate. All Right Reserved</p>
  <div class="social" aria-label="Social links"><span></span><span></span><span></span><span></span></div>
</footer>
</body>
</html>
```